Flyer for customer acquisition.

Hello, We are a sportmanagement agency from Germany and we need information flyers for customer acquisition. It should be DinA4 and should have a modern but serious design. I have uploaded a information sheet, where you can find the text and the composition, the flyer should have. I also uploaded Pictures / Images, which you can use. Of course you can use other suitable images. If they are not free, I will buy them later. On the bottom of the flyer there has been the contact information. You will find them in the download section, too. If you have questions, just write me. If I forgot something, I will update the letter :) Thank you very much!
Ich brauche zusätzliche Tage um durchzusehen

```html
<!DOCTYPE html>
<html lang="de">
<head>
<meta charset="utf-8">
<title>Nordtal Nachwuchsförderung – Flyer</title>
<link rel="stylesheet" href="https://fonts.googleapis.com/css2?family=Orbitron:wght@700;900&family=Michroma&family=Open+Sans:wght@400;700;800&display=swap">
<style>
  :root {
    --ink: #0b0d10;
    --white: #ffffff;
    --orange: #f07d1a;
    --blue: #2a9bd6;
    --box-top: #0d1014;
    --box-bottom: #1e86bb;
    --muted: #c9d1d8;
    --rule: #d7dde2;
  }
  * { box-sizing: border-box; margin: 0; padding: 0; }
  html, body { width: 707px; height: 1200px; overflow: hidden; background: var(--ink); }
  body { font-family: "Open Sans", Arial, sans-serif; color: var(--white); }

  .flyer { position: relative; width: 707px; height: 1200px; background: var(--ink); overflow: hidden; }

  .hero-photo {
    position: absolute; left: 0; top: 0; width: 707px; height: 430px;
    background:
      radial-gradient(ellipse 180px 120px at 420px 250px, rgba(210,200,180,.55), transparent 70%),
      radial-gradient(ellipse 140px 90px at 70px 240px, rgba(230,235,240,.55), transparent 70%),
      radial-gradient(ellipse 260px 160px at 330px 300px, rgba(120,110,95,.5), transparent 75%),
      linear-gradient(180deg, #1b2027 0%, #3a3a38 45%, #26282a 70%, var(--ink) 100%);
  }

  .brand-mark {
    position: absolute; left: 34px; top: 70px;
    display: flex; align-items: center; gap: 10px;
    font-family: "Open Sans", Arial, sans-serif; font-weight: 700;
    font-size: 26px; letter-spacing: 2px; color: var(--white);
  }
  .brand-mark .dot { width: 14px; height: 14px; border-radius: 50%; background: var(--white); }

  .headline { position: absolute; left: 0; top: 418px; width: 707px; text-align: center; }
  .headline .name {
    font-family: "Open Sans", Arial, sans-serif; font-weight: 800;
    font-size: 68px; line-height: 84px; letter-spacing: 4px; color: var(--white);
  }
  .headline .program {
    font-family: "Orbitron", Arial, sans-serif; font-weight: 900;
    font-size: 37px; line-height: 46px; color: var(--blue); letter-spacing: .5px;
  }

  .claim {
    position: absolute; left: 0; top: 572px; width: 707px; height: 128px;
    border-top: 2px solid var(--rule); border-bottom: 2px solid var(--rule);
    text-align: center; padding-top: 10px;
  }
  .claim .lead {
    font-family: "Orbitron", Arial, sans-serif; font-weight: 900;
    font-size: 40px; line-height: 54px; color: var(--orange); letter-spacing: 1px;
  }
  .claim .sub {
    font-family: "Michroma", Arial, sans-serif;
    font-size: 32px; line-height: 52px; color: var(--white);
  }

  .services {
    position: absolute; left: 19px; top: 714px; width: 669px;
    display: grid; grid-template-columns: repeat(3, 1fr); column-gap: 27px; row-gap: 16px;
  }
  .service {
    height: 180px; padding: 8px 10px 0;
    background: linear-gradient(180deg, var(--box-top) 0%, #13344a 55%, var(--box-bottom) 100%);
    text-align: center; font-size: 11.2px; line-height: 15px;
  }
  .service .icon {
    display: block; width: 34px; height: 34px; margin: 0 auto 4px;
    background: var(--orange);
  }
  .service h3 { font-size: 12px; line-height: 15px; font-weight: 700; color: var(--orange); margin-bottom: 3px; }
  .service p b { font-weight: 700; }

  .footnote {
    position: absolute; left: 30px; top: 1100px; width: 647px;
    text-align: center; font-size: 9.6px; line-height: 13px; color: var(--muted);
  }

  .contact {
    position: absolute; left: 19px; top: 1156px; width: 669px; height: 36px;
    display: flex; align-items: center; justify-content: center; gap: 20px;
    font-size: 18px; font-weight: 700;
  }
  .contact .item { display: flex; align-items: center; gap: 8px; white-space: nowrap; }
  .contact .sep { width: 1px; height: 22px; background: var(--rule); }
  .contact .phone { font-size: 22px; }
</style>
</head>
<body>
<div class="flyer">
  <div class="hero-photo" role="img" aria-label="Zwei Fußballspieler im Zweikampf in der Luft, Ball und Flutlicht im Nebel eines Stadions"></div>

  <div class="brand-mark"><span class="dot"></span>NORDTAL</div>

  <div class="headline">
    <div class="name">NORDTAL</div>
    <div class="program">NACHWUCHSFÖRDERUNG</div>
  </div>

  <div class="claim">
    <div class="lead">WIR BEGLEITEN DICH</div>
    <div class="sub">AUF DEINEM WEG ZUM PROFI</div>
  </div>

  <div class="services">
    <div class="service">
      <svg class="icon" viewBox="0 0 34 34"><g fill="none" stroke="#fff" stroke-width="1.6"><rect x="7" y="8" width="20" height="18"/><polyline points="10,22 15,16 19,19 24,12"/></g></svg>
      <h3>Karriereplanung</h3>
      <p><b>Wir haben deine Karriere im Blick!</b> In enger Absprache mit deinen Eltern und dir leiten wir die richtigen Maßnahmen und Schritte ein, um dein Ziel „Profifußballer“ zu realisieren</p>
    </div>
    <div class="service">
      <svg class="icon" viewBox="0 0 34 34"><g fill="none" stroke="#fff" stroke-width="1.6"><rect x="8" y="7" width="18" height="20"/><circle cx="17" cy="14" r="3"/><path d="M12 23c1-4 9-4 10 0"/></g></svg>
      <h3>Ständiger<br>Ansprechpartner</h3>
      <p>Egal um welchen Themen es sich handelt, <b>wir sind für dich da!</b> Ein vertrauensvolles und freundschaftliches Verhältnis ist uns besonders wichtig.</p>
    </div>
    <div class="service">
      <svg class="icon" viewBox="0 0 34 34"><g fill="none" stroke="#fff" stroke-width="1.6"><line x1="17" y1="7" x2="17" y2="26"/><line x1="9" y1="11" x2="25" y2="11"/><path d="M6 19l3-8 3 8z"/><path d="M22 19l3-8 3 8z"/><line x1="12" y1="26" x2="22" y2="26"/></g></svg>
      <h3>Rechtsberatung/<br>Vertragsrecht</h3>
      <p>Juristendeutsch und Kleingedrucktes? Kein Problem! <b>Wir helfen dir den Durchblick zu behalten</b> und holen immer das Beste für dich raus.</p>
    </div>
    <div class="service">
      <svg class="icon" viewBox="0 0 34 34"><g fill="none" stroke="#fff" stroke-width="1.6"><circle cx="17" cy="17" r="9"/><polygon points="17,13 21,16 19.5,20.5 14.5,20.5 13,16" fill="#fff"/></g></svg>
      <h3>Ausrüstung</h3>
      <p><b>Wir besorgen dir deine Ausrüstung!</b> Unsere Beziehungen zu den großen Sportartikelherstellern ermöglichen den Abschluss von Ausrüsterverträgen*.</p>
    </div>
    <div class="service">
      <svg class="icon" viewBox="0 0 34 34"><g fill="none" stroke="#fff" stroke-width="1.6"><path d="M8 24c3 2 7 2 10 0l8-6"/><path d="M12 20V11M15 20V9M18 20V10M21 20V12"/></g></svg>
      <h3>Vorsorge</h3>
      <p>Verletzungen gehören leider zum Fußball dazu. <b>Wir sichern dich ab,</b> indem wir eine private Zusatzkrankenversicherung für dich abschließen.</p>
    </div>
    <div class="service">
      <svg class="icon" viewBox="0 0 34 34"><g fill="none" stroke="#fff" stroke-width="1.6"><circle cx="17" cy="17" r="3"/><circle cx="9" cy="9" r="2"/><circle cx="25" cy="9" r="2"/><circle cx="9" cy="25" r="2"/><circle cx="25" cy="25" r="2"/><path d="M11 11l4 4M23 11l-4 4M11 23l4-4M23 23l-4-4"/></g></svg>
      <h3>Kooperationspartner/netzwerk</h3>
      <p>Ob Entscheidungsträger oder Experte, <b>wir kennen die richtigen Leute.</b> Zusätzlich bieten wir dir eine große Bandbreite an Leistungen, die du jederzeit in Anspruch nehmen kannst**.</p>
    </div>
  </div>

  <p class="footnote">*Die Entscheidung über das Zustandekommen eines Ausrüstervertrags obliegt dem jeweiligen Sportartikelhersteller. Ist ein Abschluss aktuell nicht möglich, erhältst du von uns 2x pro Saison neue Fußballschuhe sowie weitere Ausrüstungsgegenstände.<br>**Personal Training, Athletik-Training, Ernährungsberatung, Sportpsychologische Betreuung, uvm.</p>

  <div class="contact">
    <div class="item">
      <svg width="20" height="20" viewBox="0 0 20 20"><circle cx="10" cy="10" r="9" fill="none" stroke="#2a9bd6" stroke-width="1.6"/><rect x="5.5" y="7" width="9" height="6" fill="none" stroke="#fff" stroke-width="1.2"/><polyline points="5.5,7 10,10.5 14.5,7" fill="none" stroke="#fff" stroke-width="1.2"/></svg>
      info@nordtal-sport.de
    </div>
    <span class="sep"></span>
    <div class="item">
      <svg width="20" height="20" viewBox="0 0 20 20"><circle cx="10" cy="10" r="9" fill="none" stroke="#2a9bd6" stroke-width="1.6"/><circle cx="10" cy="10" r="5" fill="none" stroke="#fff" stroke-width="1.2"/><line x1="5" y1="10" x2="15" y2="10" stroke="#fff" stroke-width="1.2"/><ellipse cx="10" cy="10" rx="2" ry="5" fill="none" stroke="#fff" stroke-width="1.2"/></svg>
      www.nordtal-sport.de
    </div>
    <span class="sep"></span>
    <div class="item phone">
      <svg width="24" height="24" viewBox="0 0 24 24"><path d="M6 3l3 4-2 2c1 3 4 6 7 7l2-2 4 3-2 3c-7 0-15-8-15-15z" fill="none" stroke="#2a9bd6" stroke-width="1.8"/></svg>
      0711/5550123
    </div>
  </div>
</div>
</body>
</html>
```